Automotive component supplier needs a business card design

We need a business card design for our company called Velran Global Components Ltd based in the UK. We are a supplier of interior and exterior components to premium car manufacturers such as Corvel Ashby, Hadley Fenn, Marquist and Tavarelli. We would like to see a modern business card design that uses the colour blue.

Target Market(s)

Premium automotive car manufacturers.

Industry/Entity Type

Automotive

Contact Information for Business Card

Company Name : Velran Global Components Limited
Address: 17 Marlow Yard, Upper Heath, Warwick, CV31 8QL, United Kingdom
Web Address : www.velrancomponents-example.co.uk

Font styles to use
Other font styles liked:
• Helvetica

Colors
3176b5
0255a3
85acd3
cfdeed
cee9f5
85cae6
34a6d7
0692cd
9bcb3c

Requirements
Must have
• Clear company logo and a mixture of blue colours.
Nice to have
• A high quality modern image.
Should not have
• Multiple colours.

```html
<!DOCTYPE html>
<html lang="en">
<head>
<meta charset="utf-8">
<title>Velran Global Components – Business Card</title>
<link href="https://fonts.googleapis.com/css2?family=Source+Sans+3:wght@400;600;700&display=swap" rel="stylesheet">
<style>
  :root {
    --stage: #1c1c1c;
    --card-front: #f3f3f3;
    --card-back: #fafafa;
    --brand-blue: #0692cd;
    --ink: #1e1e1e;
  }
  * { margin: 0; padding: 0; box-sizing: border-box; }
  html, body {
    width: 1200px; height: 900px; overflow: hidden;
    background: var(--stage);
    font-family: "Source Sans 3", "Helvetica Neue", Arial, sans-serif;
  }
  .canvas { position: relative; width: 1200px; height: 900px; }
  .card {
    position: absolute; top: 184px; height: 490px;
    border-radius: 12px; overflow: hidden;
  }
  .card--front { left: 298px; width: 302px; background: var(--card-front); }
  .card--back { left: 645px; width: 304px; background: var(--card-back); }

  .front-brand {
    position: absolute; top: 98px; left: 0; right: 0;
    text-align: center;
    font-size: 56px; font-weight: 700; color: var(--brand-blue);
    line-height: 64px; letter-spacing: 0.5px;
  }

  .person { position: absolute; top: 237px; left: 0; right: 0; text-align: center; }
  .person__name { font-size: 17px; font-weight: 700; color: var(--brand-blue); line-height: 22px; }
  .person__role { font-size: 13px; color: var(--ink); line-height: 16px; }

  .contact {
    position: absolute; top: 301px; left: 0; right: 0;
    text-align: center; font-size: 13px; line-height: 17.5px; color: var(--ink);
    list-style: none;
  }
  .address {
    position: absolute; top: 384px; left: 0; right: 0;
    text-align: center; font-size: 13px; line-height: 18px; color: var(--ink);
    font-style: normal;
  }

  .back-brand {
    position: absolute; left: 50%; top: 50%;
    transform: translate(-50%, -50%) rotate(-90deg);
    display: flex; flex-direction: column; align-items: center;
    white-space: nowrap; color: var(--brand-blue); font-weight: 600;
    text-transform: uppercase;
  }
  .back-brand__name {
    font-size: 80px; line-height: 62px; letter-spacing: 8px;
  }
  .back-brand__tagline {
    font-size: 22px; line-height: 26px; letter-spacing: 7px; margin-top: 10px;
  }
</style>
</head>
<body>
<main class="canvas">
  <section class="card card--front" aria-label="Business card front">
    <p class="front-brand">Velran</p>
    <div class="person">
      <p class="person__name">Elias Thorne</p>
      <p class="person__role">Director</p>
    </div>
    <ul class="contact">
      <li>01926 555 014</li>
      <li>01926 555 027</li>
      <li>hello@velran-example.co.uk</li>
      <li>www.velrancomponents-example.co.uk</li>
    </ul>
    <address class="address">17 Marlow Yard, Upper Heath,<br>Warwick, CV31 8QL, United Kingdom</address>
  </section>

  <section class="card card--back" aria-label="Business card back">
    <div class="back-brand">
      <span class="back-brand__name">Velran</span>
      <span class="back-brand__tagline">Global Components</span>
    </div>
  </section>
</main>
</body>
</html>
```